RTavenor Business Cards & Letterhead

I have a logo but need a design for some new business cards. We are a Design-Build Firm that specializes in the design and construction of commercial projects.
the cards need to be professional. no cartoon stuff.
i would like to have the cards in AI format so I can update the card as needed. Logo is provided.
Our Address is: 4187 Marlowe Ct. Linden, West Virginia 27614

```html
<!DOCTYPE html>
<html lang="en">
<head>
<meta charset="utf-8">
<title>RTavenor Business Card</title>
<link href="https://fonts.googleapis.com/css2?family=Roboto:wght@400;700;900&display=swap" rel="stylesheet">
<style>
  :root {
    --backdrop: #979797;
    --card-white: #ffffff;
    --brand-blue: #005b8f;
    --ink-grey: #555555;
  }
  html, body {
    margin: 0;
    padding: 0;
    width: 1200px;
    height: 1000px;
    overflow: hidden;
    background: var(--backdrop);
  }
  .canvas {
    position: relative;
    width: 1200px;
    height: 1000px;
    font-family: "Roboto", Arial, sans-serif;
  }
  .card-shapes {
    position: absolute;
    inset: 0;
  }
  .front-card { fill: var(--card-white); }
  .back-card { fill: var(--brand-blue); }

  .wordmark {
    position: absolute;
    left: 168px;
    top: 590px;
    transform: translate(-50%, -50%) rotate(-90deg);
    display: flex;
    align-items: center;
    gap: 12px;
    white-space: nowrap;
  }
  .wordmark-square {
    width: 18px;
    height: 18px;
    background: var(--brand-blue);
  }
  .wordmark-name {
    font-weight: 900;
    font-size: 36px;
    letter-spacing: 1px;
    color: var(--ink-grey);
  }

  .contact {
    position: absolute;
    left: 281px;
    top: 421px;
    color: var(--ink-grey);
  }
  .contact-name {
    margin: 0;
    font-weight: 700;
    font-size: 21px;
    line-height: 28px;
  }
  .contact-title {
    margin: 0;
    font-size: 20px;
    line-height: 27px;
  }
  .contact-rule {
    width: 75px;
    height: 3px;
    background: var(--brand-blue);
    margin: 10px 0 24px;
  }
  .contact-lines {
    margin: 0 0 26px;
    font-size: 20px;
    line-height: 28px;
    font-style: normal;
  }
  .contact-web {
    margin: 0;
    font-weight: 700;
    font-size: 20px;
    line-height: 28px;
    color: var(--brand-blue);
  }
</style>
</head>
<body>
<div class="canvas">
  <svg class="card-shapes" width="1200" height="1000" viewBox="0 0 1200 1000" aria-hidden="true">
    <path class="front-card" d="M230 230 H540 A50 50 0 0 1 590 280 V550 A220 220 0 0 1 370 770 H113 A50 50 0 0 1 63 720 V410 H230 Z"/>
    <path class="back-card" d="M792 230 H1102 A50 50 0 0 1 1152 280 V550 A220 220 0 0 1 932 770 H675 A50 50 0 0 1 625 720 V410 H792 Z"/>
  </svg>

  <div class="wordmark">
    <span class="wordmark-square"></span>
    <span class="wordmark-name">TAVENOR</span>
  </div>

  <div class="contact">
    <p class="contact-name">ROBERT TAVENOR</p>
    <p class="contact-title">President</p>
    <div class="contact-rule"></div>
    <address class="contact-lines">4187 Marlowe Ct. Linden<br>West Virginia 27614</address>
    <p class="contact-lines">919-555-0148<br>robert@rtavenor.com</p>
    <p class="contact-web">rtavenor.com</p>
  </div>
</div>
</body>
</html>
```